Real Estate Wordpress Landing Page

I'm looking to a landing page dedicated to my real estate brokerage that's catered to promoting that my company provides 1.5% listings to home sellers... I have a couple examples that I'm really looking towards mocking in a version with similar color schemes using my current company colors/website.

http://harbelo.com/
https://www.quarvantis.com/about/one-percent-listing-fee

My brokerage company website is http://www.brightmarrow.us/

Target Market(s)

real estate home sellers & buyers

Industry/Entity Type

Real Estate

Coding

Coded - Design and coding required

Number of Pages Required

1 page

Colors
3176b5
0255a3
eaf1f7
cedeed

Requirements
Must have
• Company website colors - http://www.brightmarrow.us/
• Something around the lines of this website page - http://harbelo.com/
• Wordpress compatibility

```html
<!DOCTYPE html>
<html lang="en">
<head>
<meta charset="utf-8">
<title>Calder Voss, Lic. Real Estate Broker — Bright Marrow Realty</title>
<link href="https://fonts.googleapis.com/css2?family=Oswald:wght@500;600;700&family=Roboto:wght@400;500;700&display=swap" rel="stylesheet">
<style>
  :root{
    --blue:#0255a3;
    --blue-mid:#3176b5;
    --blue-pale:#eaf1f7;
    --blue-soft:#cedeed;
    --ink:#333333;
    --grey-bg:#f4f4f4;
    --footer:#3d3b3a;
    --white:#ffffff;
  }
  *{box-sizing:border-box;margin:0;padding:0}
  html,body{width:1200px;height:2344px;overflow:hidden}
  body{position:relative;font-family:"Roboto",Arial,sans-serif;color:var(--ink);background:var(--white)}
  .abs{position:absolute}

  /* hero */
  .hero{position:absolute;left:0;top:0;width:1200px;height:725px;
    background:linear-gradient(180deg,#3a4350 0%,#5a6068 35%,#6b6a66 62%,#4d5a3a 86%,#3e4a2c 100%)}
  .hero-shade{position:absolute;inset:0;background:rgba(20,24,30,.35)}
  .hero-rule{position:absolute;left:0;top:722px;width:1200px;height:4px;background:var(--blue)}
  .hero-notch{position:absolute;left:576px;top:725px}
  .brand-box{position:absolute;left:161px;top:0;width:131px;height:106px;background:var(--white);
    display:flex;align-items:center;justify-content:center;gap:7px;flex-direction:column}
  .brand-dot{width:14px;height:14px;background:var(--blue)}
  .brand-name{font-family:"Roboto",sans-serif;font-weight:700;font-size:15px;color:var(--blue);text-align:center;line-height:1.1}
  .contact{position:absolute;top:34px;color:var(--white);font-size:12.5px;font-weight:500;line-height:19px}
  .contact svg{position:absolute;left:-30px;top:4px}
  .socials{position:absolute;left:931px;top:44px;display:flex;gap:4px}
  .socials span{width:18px;height:18px;border-radius:50%;background:var(--white)}
  .hero-title{position:absolute;left:161px;top:214px;font-family:"Oswald",sans-serif;font-weight:700;
    color:var(--white);font-size:64px;line-height:88px;letter-spacing:.5px}
  .hero-lede{position:absolute;left:161px;top:486px;width:500px;color:var(--white);font-size:14.5px;font-weight:700;line-height:23px}

  .lead-form{position:absolute;left:737px;top:228px;width:302px;height:497px;background:rgba(255,255,255,.72);padding:0 19px}
  .lead-form h2{margin-top:42px;font-size:16.5px;font-weight:500;color:var(--blue)}
  .field{display:block;width:263px;height:38px;background:var(--white);margin-top:15px;font-size:11px;color:#555;padding:12px 12px;position:relative}
  .field:first-of-type{margin-top:12px}
  .field.select .arrow{position:absolute;right:0;top:0;width:36px;height:38px;background:var(--blue);display:flex;align-items:center;justify-content:center}
  .field.message{height:97px}
  .submit{display:block;width:263px;height:38px;margin-top:15px;background:var(--blue);color:var(--white);font-size:13px;font-weight:700;text-align:center;line-height:38px}

  /* listings */
  .listings{position:absolute;left:0;top:729px;width:1200px;height:477px;background:var(--grey-bg)}
  .section-title{position:absolute;width:1200px;text-align:center;font-family:"Oswald",sans-serif;font-weight:600;color:var(--blue)}
  .listings .section-title{top:80px;font-size:28px}
  .card{position:absolute;top:157px;width:269px;height:253px;background:var(--white)}
  .card-photo{width:269px;height:183px}
  .saved-badge{position:absolute;background:var(--blue);color:var(--white);font-size:11px;font-weight:700;padding:0 12px;height:27px;line-height:27px}
  .card .saved-badge{right:-6px;top:28px}
  .card-text{padding:17px 12px 0;font-size:11px;line-height:19px;color:#333;font-weight:500}

  /* guarantee */
  .guarantee .section-title{top:1265px;font-size:31px;line-height:45px;font-weight:600}
  .device{position:absolute;left:188px;top:1441px;width:487px;height:306px;border-radius:14px 14px 6px 6px;
    background:linear-gradient(180deg,#2b2b2d 0%,#6f7378 55%,#b8b4ad 80%,#8d8f93 100%)}
  .device .saved-badge{left:77px;top:188px}
  .device-caption{position:absolute;left:77px;top:227px;color:var(--white);font-size:12px;font-weight:700}
  .sell{position:absolute;left:708px;top:1466px;width:320px}
  .sell h3{font-size:13.5px;font-weight:700;text-decoration:underline;color:#111}
  .sell ul{list-style:none;margin-top:14px}
  .sell li{font-size:11px;line-height:20px;color:#555;padding-left:15px;position:relative}
  .sell li svg{position:absolute;left:0;top:6px}
  .sell p{margin-top:13px;font-size:12px;font-weight:700;line-height:22px;color:#444}
  .btn{position:absolute;top:1634px;height:36px;font-size:12px;font-weight:700;text-align:center;line-height:34px}
  .btn-solid{left:708px;width:111px;background:var(--blue);color:var(--white);border:1px solid var(--blue)}
  .btn-outline{left:827px;width:112px;background:var(--white);color:var(--blue);border:1.5px solid var(--blue)}
  .slider-nav{position:absolute;left:708px;top:1700px;display:flex;gap:4px}
  .slider-nav span{width:21px;height:17px;background:#e3e3e3;display:flex;align-items:center;justify-content:center}

  /* call band */
  .call-band{position:absolute;left:0;top:1813px;width:1200px;height:353px;
    background:linear-gradient(180deg,#4c5566 0%,#3d4250 45%,#5a4a3e 75%,#2f2d2e 100%)}
  .call-band .shade{position:absolute;inset:0;background:rgba(20,20,28,.3)}
  .call-title{position:absolute;top:60px;width:1200px;text-align:center;font-family:"Oswald",sans-serif;font-weight:700;font-size:36px;color:var(--white)}
  .call-text{position:absolute;top:127px;width:1200px;text-align:center;color:var(--white);font-size:13.5px;font-weight:700;line-height:22px}
  .call-phone{position:absolute;top:188px;width:1200px;text-align:center;color:var(--white);font-size:19px;font-weight:700}
  .call-phone svg{vertical-align:-3px;margin-right:10px}
  .call-band .btn{top:240px;left:544px;width:109px;height:38px;line-height:38px;background:var(--blue);color:var(--white)}

  /* strip + footer */
  .promo{position:absolute;top:2190px;width:1200px;text-align:center;font-size:20px;color:var(--ink)}
  .promo strong{color:var(--blue);font-weight:400}
  .promo-sub{position:absolute;top:2222px;width:1200px;text-align:center;font-size:11.5px;font-weight:500;color:#333}
  .site-footer{position:absolute;left:0;top:2266px;width:1200px;height:78px;background:var(--footer);color:#a7a5a3;text-align:center;font-size:11.5px}
  .site-footer .row1{margin-top:17px}
  .site-footer .row2{margin-top:10px}
  .sep{margin:0 14px}
</style>
</head>
<body>

<header class="hero" role="img" aria-label="Two-storey suburban home with a listing sign on the front lawn under a cloudy sky">
  <div class="hero-shade"></div>
</header>
<div class="hero-rule"></div>
<svg class="hero-notch abs" width="48" height="20" viewBox="0 0 48 20"><path d="M0 0H48L24 20Z" fill="var(--blue)"/></svg>

<div class="brand-box">
  <span class="brand-dot"></span>
  <span class="brand-name">Bright Marrow<br>Realty</span>
</div>

<div class="contact" style="left:395px">
  <svg width="16" height="16" viewBox="0 0 24 24"><path d="M6.6 10.8a15 15 0 0 0 6.6 6.6l2.2-2.2c.3-.3.7-.4 1-.2 1.1.4 2.3.6 3.6.6.6 0 1 .4 1 1V20c0 .6-.4 1-1 1A17 17 0 0 1 3 4c0-.6.4-1 1-1h3.5c.6 0 1 .4 1 1 0 1.3.2 2.5.6 3.6.1.3 0 .7-.2 1z" fill="#fff"/></svg>
  555-014-7930<br>contact@brightmarrow.us
</div>
<div class="contact" style="left:625px;width:260px">
  <svg width="16" height="18" viewBox="0 0 24 26"><path d="M12 1a8 8 0 0 0-8 8c0 6 8 14 8 14s8-8 8-14a8 8 0 0 0-8-8zm0 11a3 3 0 1 1 0-6 3 3 0 0 1 0 6z" fill="none" stroke="#fff" stroke-width="2"/></svg>
  2400 Harbor Pointe Blvd, Ste 310 Coral Vale, FL 33490 contact@brightmarrow.us
</div>
<div class="socials" aria-label="Social links"><span></span><span></span><span></span><span></span><span></span></div>

<h1 class="hero-title">CALDER VOSS, Lic.<br>Real Estate<br>Broker</h1>
<p class="hero-lede">On average, our customers save $5,600 when they list with us...andthey still receive top marketing and quality professional service!</p>

<form class="lead-form">
  <h2>List for 1.5% Commission</h2>
  <span class="field">Name</span>
  <span class="field">E-mail</span>
  <span class="field">Phone Number</span>
  <span class="field select">I'm Interested In<span class="arrow"><svg width="11" height="8" viewBox="0 0 11 8"><path d="M0 0H11L5.5 8Z" fill="#fff"/></svg></span></span>
  <span class="field message">Message</span>
  <span class="submit">Submit</span>
</form>

<section class="listings">
  <h2 class="section-title">Latest Property</h2>
  <article class="card" style="left:161px">
    <div class="card-photo" role="img" aria-label="Two-storey house with a garage and green lawn" style="background:linear-gradient(180deg,#cfe0ec 0%,#e8e2d4 45%,#c9bfa8 70%,#6f8f4a 100%)"></div>
    <span class="saved-badge">Saved $4,650</span>
    <p class="card-text">4812 Willowmere Lane Palm Hollow,<br>FL 33481 - $310,000</p>
  </article>
  <article class="card" style="left:462px">
    <div class="card-photo" role="img" aria-label="Bright living room with sofas and a wall-mounted television" style="background:linear-gradient(180deg,#dcdcdc 0%,#bfc1c4 45%,#8e9196 75%,#d6d6d6 100%)"></div>
    <span class="saved-badge">Saved $7,485</span>
    <p class="card-text">718 Seabright Boulevard, 204 Coral Vale,<br>FL 33492 - $499,000</p>
  </article>
  <article class="card" style="left:762px">
    <div class="card-photo" role="img" aria-label="Two-storey townhouse with palm trees and a garage" style="background:linear-gradient(180deg,#bcd6ea 0%,#e9e1c8 45%,#d7c9a0 70%,#5f8a44 100%)"></div>
    <span class="saved-badge">Saved $4,650</span>
    <p class="card-text">10236 Amberfield Circle Palm Hollow,<br>FL 33487 - $310,000</p>
  </article>
</section>

<section class="guarantee">
  <h2 class="section-title">30 Day Listing Service GUARANTEED. Save thousands $$$ listing<br>with us!Morbi eu sem felis. Integer faucibus ligula vitae<br>enim vestibulum iaculis.</h2>
  <div class="device" role="img" aria-label="Laptop showing a furnished living room listing">
    <span class="saved-badge">Saved $4,200</span>
    <span class="device-caption">327 s Fairway Ridge drive Dunmere,FL33495 - $550,000</span>
  </div>
  <div class="sell">
    <h3>SELL WITH BRIGHT MARROW &amp; SAVE $$$</h3>
    <ul>
      <li><svg width="10" height="9" viewBox="0 0 10 9"><path d="M1 5l3 3 5-7" fill="none" stroke="var(--blue)" stroke-width="2"/></svg>Professional Real Estate Photography</li>
      <li><svg width="10" height="9" viewBox="0 0 10 9"><path d="M1 5l3 3 5-7" fill="none" stroke="var(--blue)" stroke-width="2"/></svg>Complimentary Comparative Market Analysis (CMA)</li>
      <li><svg width="10" height="9" viewBox="0 0 10 9"><path d="M1 5l3 3 5-7" fill="none" stroke="var(--blue)" stroke-width="2"/></svg>FREE Consultation with Real Estate Professional</li>
    </ul>
    <p>Lorem ipsum dolor sit amet, consectetur adip-<br>iscingelit. Praesent rhoncus nibh nisl</p>
  </div>
  <span class="btn btn-solid">CALL US !</span>
  <span class="btn btn-outline">555-019-6902</span>
  <div class="slider-nav">
    <span><svg width="10" height="6" viewBox="0 0 10 6"><path d="M10 3H1M3 1L1 3l2 2" fill="none" stroke="#333"/></svg></span>
    <span><svg width="10" height="6" viewBox="0 0 10 6"><path d="M0 3h9M7 1l2 2-2 2" fill="none" stroke="#333"/></svg></span>
  </div>
</section>

<section class="call-band" role="img" aria-label="Modern two-storey house lit at dusk">
  <div class="shade"></div>
  <h2 class="call-title">CALL US TODAY AND SAVE THOUSANDS $$$</h2>
  <p class="call-text">On average, our customers save $5,600 when they list with us... andthey still<br>receive top marketing and quality professional service</p>
  <p class="call-phone"><svg width="18" height="18" viewBox="0 0 24 24"><path d="M6.6 10.8a15 15 0 0 0 6.6 6.6l2.2-2.2c.3-.3.7-.4 1-.2 1.1.4 2.3.6 3.6.6.6 0 1 .4 1 1V20c0 .6-.4 1-1 1A17 17 0 0 1 3 4c0-.6.4-1 1-1h3.5c.6 0 1 .4 1 1 0 1.3.2 2.5.6 3.6.1.3 0 .7-.2 1z" fill="#fff"/></svg>555-019-6902</p>
  <span class="btn">CALL US !</span>
</section>

<p class="promo"><strong>LIST FOR 1.5% COMMISSION,</strong> And Receive Top Marketing from Real Estate Pro!</p>
<p class="promo-sub">Contact Calder Voss to Begin Your Real Estate Search!</p>

<footer class="site-footer">
  <p class="row1">555-019-6902<span class="sep">|</span>contact@brightmarrow.us<span class="sep">|</span>2400 Harbor Pointe Blvd, Ste 310, Coral Vale, FL 33490</p>
  <p class="row2">2018 Brightmarrow. All rights reserved.</p>
</footer>

</body>
</html>
```